Quorva - corporate Business Card

We need a good look and innovative business card for a new start up company based in Los Angeles called "Quorva". We are in a payment business, including payment card, app, and ewallet. We are expert in online payment and Card not present (CNP) transaction.
We need an innovative, modern business card.

Our logo font is Aero Matics

Target Market(s)

Startup - Bank - Online Payment - Card Manufacturing

Industry/Entity Type

Startup

Contact Information for Business Card

phone: 555 014 7396 - Address: 4172 Marlowe blvd, Halden Park, OR 97299

Requirements
Must have
• Message: innovative, professional, expert, high tech, trust, online payment expert, security
Nice to have
• no comment
Should not have
• no Comment

```html
<!DOCTYPE html>
<html lang="en">
<head>
<meta charset="utf-8">
<title>Quorva – Business Card</title>
<link rel="stylesheet" href="https://fonts.googleapis.com/css2?family=Open+Sans:wght@400;600;700&display=swap">
<style>
  :root {
    --brand-red: #b51f2e;
    --paper: #ffffff;
    --ink-grey: #6b6b6b;
    --backdrop: #3a3634;
  }
  * { margin: 0; padding: 0; box-sizing: border-box; }
  html, body {
    width: 1200px;
    height: 780px;
    overflow: hidden;
    background: var(--backdrop);
    font-family: "Open Sans", Arial, sans-serif;
  }
  .canvas {
    position: relative;
    width: 1200px;
    height: 780px;
  }
  .card {
    position: absolute;
    width: 540px;
    height: 320px;
    overflow: hidden;
    box-shadow: 0 10px 30px rgba(0,0,0,0.45);
  }

  /* Front */
  .card-front {
    left: 50px;
    top: 70px;
    background: var(--paper);
    padding: 16px;
  }
  .card-front .panel {
    width: 100%;
    height: 100%;
    background: var(--brand-red);
    display: flex;
    align-items: center;
    justify-content: center;
  }
  .brand {
    display: flex;
    align-items: center;
    gap: 14px;
  }
  .brand-dot {
    border-radius: 50%;
    flex: none;
  }
  .brand-name {
    font-weight: 700;
    letter-spacing: 1px;
    line-height: 1;
  }
  .card-front .brand-dot { width: 66px; height: 66px; background: var(--paper); }
  .card-front .brand-name { font-size: 62px; color: var(--paper); }

  /* Back */
  .card-back {
    left: 610px;
    top: 390px;
    background: var(--brand-red);
  }
  .card-back .backdrop {
    position: absolute;
    inset: 0;
  }
  .card-back .content {
    position: absolute;
    left: 30px;
    top: 34px;
  }
  .card-back .brand-dot { width: 50px; height: 50px; background: var(--brand-red); }
  .card-back .brand-name { font-size: 48px; color: var(--brand-red); }
  .holder {
    margin-top: 26px;
  }
  .holder-name {
    font-size: 17px;
    font-weight: 700;
    color: var(--brand-red);
    line-height: 1.1;
  }
  .holder-role {
    font-size: 13px;
    color: var(--ink-grey);
  }
  .contact {
    margin-top: 22px;
    font-size: 12.5px;
    color: var(--ink-grey);
    line-height: 1.6;
  }
  .contact-line {
    display: flex;
    align-items: center;
    gap: 7px;
  }
  .phone-icon { width: 15px; height: 15px; flex: none; }
</style>
</head>
<body>
<main class="canvas">

  <section class="card card-front" aria-label="Business card front">
    <div class="panel">
      <div class="brand">
        <span class="brand-dot"></span>
        <span class="brand-name">quorva</span>
      </div>
    </div>
  </section>

  <section class="card card-back" aria-label="Business card back">
    <svg class="backdrop" width="540" height="320" viewBox="0 0 540 320" aria-hidden="true">
      <defs>
        <clipPath id="inner-area">
          <rect x="14" y="14" width="512" height="292"/>
        </clipPath>
      </defs>
      <rect x="14" y="14" width="512" height="292" fill="var(--paper)"/>
      <g clip-path="url(#inner-area)">
        <circle cx="500" cy="250" r="170" fill="var(--brand-red)"/>
      </g>
    </svg>

    <div class="content">
      <div class="brand">
        <span class="brand-dot"></span>
        <span class="brand-name">quorva</span>
      </div>
      <div class="holder">
        <p class="holder-name">Dana Whitlow</p>
        <p class="holder-role">Managing Director</p>
      </div>
      <div class="contact">
        <p class="contact-line">
          <svg class="phone-icon" viewBox="0 0 16 16" aria-hidden="true">
            <circle cx="8" cy="8" r="8" fill="var(--brand-red)"/>
            <path d="M5.2 4.2 L6.6 4 L7.3 5.8 L6.4 6.6 Q7.1 8.4 9.2 9.5 L10 8.6 L11.9 9.3 L11.7 10.8 Q10.9 11.9 9.4 11.5 Q5.3 10.1 4.3 6 Q4.1 4.8 5.2 4.2 Z" fill="var(--paper)"/>
          </svg>
          555 014 7396
        </p>
        <p class="contact-line">4172 Marlowe blvd, Halden Park, OR 97299</p>
      </div>
    </div>
  </section>

</main>
</body>
</html>
```